Automotive eCommerce Business looking for a business card design

Looking for a clean and simple business card design. Our company name is "Brindle Auto" and we are a company specializing in the ecommerce sales of automotive parts, specifically for pick up trucks and large SUVs. Our company colours are red, black, and white.

Feel free to use the logo provided or create a new logo that you seem fit. Looking forward to your creative ideas!

Industry/Entity Type

Automotive

Contact Information for Business Card

We were thinking of a possibly two-sided design featuring just the logo and company name on one side, and personal information on the other side. Single sided designs will be considered as well.

Font styles to use
Serif
Sans Serif
Decorative

Colors
ec1f27
ffffff
000000

Requirements
Must have
• Space for employee's name, title, phone number and email address, along with the company address and website somewhere.

```html
<!DOCTYPE html>
<html lang="en">
<head>
<meta charset="utf-8">
<title>Brindle Auto – Business Card</title>
<link rel="stylesheet" href="https://fonts.googleapis.com/css2?family=Libre+Baskerville:wght@700&family=Arimo:wght@400;700&display=swap">
<style>
  :root {
    --brand-red: #a11b22;
    --brand-red-dark: #7e1419;
    --ink: #111111;
    --paper: #ffffff;
    --paper-shade: #ececec;
    --backdrop: #2b2b2b;
  }
  * { box-sizing: border-box; margin: 0; padding: 0; }
  html, body {
    width: 1200px; height: 997px; overflow: hidden;
    background: var(--backdrop);
  }
  .stage {
    position: relative; width: 1200px; height: 997px;
  }
  .card {
    position: absolute; top: 347px;
    width: 530px; height: 303px;
    background: linear-gradient(160deg, var(--paper) 40%, var(--paper-shade));
    overflow: hidden;
    box-shadow: 0 14px 30px rgba(0,0,0,.55);
  }
  .card--front { left: 50px; }
  .card--back { left: 620px; }
  .card__shape { position: absolute; inset: 0; width: 100%; height: 100%; }

  .brand-name {
    font-family: "Libre Baskerville", Georgia, serif;
    font-weight: 700; color: var(--brand-red);
    white-space: nowrap;
  }
  .card--front .brand-lockup {
    position: absolute; left: 42px; top: 64px;
    display: flex; align-items: center; gap: 14px;
  }
  .brand-mark {
    width: 30px; height: 30px; background: var(--brand-red);
  }
  .card--front .brand-name { font-size: 44px; letter-spacing: -0.5px; }
  .website {
    position: absolute; left: 250px; top: 210px;
    font-family: "Arimo", Arial, sans-serif; font-size: 13px;
    letter-spacing: 3.5px; color: var(--paper);
    transform: rotate(-22deg); transform-origin: left center;
    white-space: nowrap;
  }

  .card--back .brand-name {
    position: absolute; top: 38px; left: 0; right: 0;
    text-align: center; font-size: 30px;
  }
  .person {
    position: absolute; top: 100px; left: 0; right: 0; text-align: center;
    font-family: "Arimo", Arial, sans-serif;
  }
  .person__name {
    font-size: 21px; font-weight: 700; color: var(--brand-red);
    letter-spacing: .5px;
  }
  .person__title { font-size: 13px; color: var(--ink); margin-top: 1px; }
  .contact {
    position: absolute; top: 190px; left: 0; right: 0; text-align: center;
    font-family: "Arimo", Arial, sans-serif; color: var(--paper);
    font-size: 14.5px; line-height: 1.42; letter-spacing: .3px;
  }
  .contact__icons {
    display: flex; justify-content: center; gap: 10px; margin-bottom: 5px;
  }
  .contact__icon { width: 16px; height: 16px; }
</style>
</head>
<body>
<main class="stage">

  <section class="card card--front" aria-label="Card front">
    <svg class="card__shape" viewBox="0 0 530 303" preserveAspectRatio="none" aria-hidden="true">
      <path d="M0 303 L0 292 C150 215 320 130 530 92 L530 303 Z" fill="var(--brand-red)"/>
      <path d="M0 292 C150 210 320 120 530 80 C330 112 150 196 0 292 Z" fill="var(--ink)"/>
    </svg>
    <div class="brand-lockup">
      <span class="brand-mark"></span>
      <span class="brand-name">Brindle Auto</span>
    </div>
    <p class="website">WWW.BRINDLEAUTO.COM</p>
  </section>

  <section class="card card--back" aria-label="Card back">
    <svg class="card__shape" viewBox="0 0 530 303" preserveAspectRatio="none" aria-hidden="true">
      <path d="M0 303 L0 240 C140 165 330 122 530 132 L530 303 Z" fill="var(--brand-red)"/>
      <path d="M110 206 C230 150 380 118 525 118 C380 110 230 138 110 206 Z" fill="var(--ink)"/>
    </svg>
    <p class="brand-name">Brindle Auto</p>
    <div class="person">
      <p class="person__name">MAREN HOLT</p>
      <p class="person__title">Owner</p>
    </div>
    <div class="contact">
      <div class="contact__icons">
        <svg class="contact__icon" viewBox="0 0 16 16" aria-label="Phone"><circle cx="8" cy="8" r="8" fill="var(--paper)"/><path d="M5 4.5 L6.5 4.5 L7 6.5 L6.2 7.2 C6.8 8.4 7.6 9.2 8.8 9.8 L9.5 9 L11.5 9.5 L11.5 11 C8 11.2 4.8 8 5 4.5 Z" fill="var(--brand-red-dark)"/></svg>
        <svg class="contact__icon" viewBox="0 0 16 16" aria-label="Email"><circle cx="8" cy="8" r="8" fill="var(--paper)"/><rect x="4" y="5.2" width="8" height="5.6" fill="var(--brand-red-dark)"/><path d="M4 5.2 L8 8.4 L12 5.2" stroke="var(--paper)" stroke-width=".8" fill="none"/></svg>
        <svg class="contact__icon" viewBox="0 0 16 16" aria-label="Address"><circle cx="8" cy="8" r="8" fill="var(--paper)"/><path d="M8 12.5 C6 10 5 8.5 5 7 A3 3 0 0 1 11 7 C11 8.5 10 10 8 12.5 Z" fill="var(--brand-red-dark)"/><circle cx="8" cy="7" r="1.1" fill="var(--paper)"/></svg>
      </div>
      <p>04120-318845-0</p>
      <p>name@brindle-parts.de</p>
      <p>Lindauer Str. 18,70174 Stuttgart</p>
    </div>
  </section>

</main>
</body>
</html>
```